Vegetable Grower Expo Backdrop

I need an 8x8 backdrop for an expo booth. We are a vegetable grower and have very limited graphics to work with. I have uploaded our logo which may not be the correct format and need to be updated for quality to print at that size. Need something quick and simple. Expo is August 18th

Target Market(s)

Retail and Wholesale buyers

Industry/Entity Type

Produce

Colors

Designer to choose colors to be used in the design.

Requirements
Must have
• Logo
Nice to have
• I am open to ideas!
Should not have
• Keep it simple and bottom 1/4 will be covered with samples so focus on top 3/4 of banner

```html
<!DOCTYPE html>
<html lang="en">
<head>
<meta charset="utf-8">
<title>Vegetable Grower Expo 2025 Backdrop</title>
<link rel="stylesheet" href="https://fonts.googleapis.com/css2?family=Bebas+Neue&family=Poppins:wght@500&display=swap">
<style>
  :root {
    --page: #f6f5fa;
    --white: #ffffff;
    --green-bright: #2aa620;
    --green-mid: #1c7d2a;
    --green-deep: #0f4a2c;
    --navy: #0a1638;
    --lime: #9be34a;
    --lime-deep: #3f9a16;
    --field-dark: #2c3a2c;
    --field-leaf: #3f8a2e;
    --greenhouse: #d9e2df;
  }
  * { margin: 0; padding: 0; box-sizing: border-box; }
  html, body {
    width: 1032px; height: 1200px; overflow: hidden;
    background: var(--page);
  }
  .backdrop {
    position: absolute; left: 16px; top: 111px;
    width: 1000px; height: 978px; overflow: hidden;
    background: var(--navy);
  }
  .backdrop-art { position: absolute; inset: 0; width: 1000px; height: 978px; }
  .title {
    position: absolute; left: 60px;
    font-family: "Bebas Neue", "Oswald", sans-serif;
    color: var(--white); line-height: 1; white-space: nowrap;
  }
  .title-main { top: 40px; font-size: 174px; letter-spacing: 3px; }
  .title-sub { top: 201px; font-size: 110px; letter-spacing: 2px; }
  .year-tag {
    position: absolute; left: 60px; top: 327px; width: 250px; height: 107px;
    background: var(--green-bright); border-radius: 7px;
    display: flex; align-items: center; justify-content: center;
    font-family: "Bebas Neue", "Oswald", sans-serif;
    font-size: 118px; color: var(--white); line-height: 1; padding-top: 10px;
    letter-spacing: 2px;
  }
  .photo-round {
    position: absolute; border-radius: 50%;
    border: 7px solid var(--white);
  }
  .photo-seedling {
    left: 444px; top: 389px; width: 312px; height: 312px;
    background: radial-gradient(circle at 55% 30%, #fff6cf 0%, #e9dc8e 35%, #9c8a4e 65%, #6b4e2e 100%);
  }
  .photo-harvest {
    left: 63px; top: 486px; width: 340px; height: 340px;
    background: radial-gradient(circle at 45% 55%, #d8352a 0%, #c0402a 25%, #4f9a32 55%, #244a3a 85%, #1e3350 100%);
  }
  .brand-badge {
    position: absolute; left: 683px; top: 169px; width: 264px; height: 264px;
    border-radius: 50%; border: 8px solid var(--white);
    background: linear-gradient(180deg, #0f3d33 0%, #12203f 100%);
    display: flex; align-items: center; justify-content: center; text-align: center;
    font-family: "Bebas Neue", "Oswald", sans-serif;
    font-size: 44px; line-height: 1.05; color: var(--white); letter-spacing: 1px;
  }
  .web-address {
    position: absolute; left: 232px; top: 866px;
    display: flex; align-items: center; gap: 26px;
    font-family: "Poppins", sans-serif; font-weight: 500;
    font-size: 52px; color: var(--white); line-height: 1;
  }
  .web-address svg { width: 36px; height: 36px; }
</style>
</head>
<body>
<main class="backdrop">
  <svg class="backdrop-art" viewBox="0 0 1000 978" aria-hidden="false">
    <defs>
      <linearGradient id="fieldTone" x1="0" y1="0" x2="0" y2="1">
        <stop offset="0" stop-color="#e6ece9"/>
        <stop offset="0.42" stop-color="#b9c7bf"/>
        <stop offset="0.55" stop-color="#4f9a36"/>
        <stop offset="1" stop-color="#24402a"/>
      </linearGradient>
      <linearGradient id="panelTone" x1="0.5" y1="0" x2="0.2" y2="1">
        <stop offset="0" stop-color="#23a41d"/>
        <stop offset="0.45" stop-color="#17602f"/>
        <stop offset="1" stop-color="#081540"/>
      </linearGradient>
    </defs>
    <rect class="field-photo" role="img" aria-label="Photo: rows of lettuce growing under a polytunnel greenhouse" width="1000" height="978" fill="url(#fieldTone)"/>
    <path class="curve-accent" d="M985 0 C 930 250 790 440 0 735 L 0 708 C 740 430 900 240 955 0 Z" fill="var(--lime-deep)"/>
    <path class="curve-accent" d="M1000 20 C 960 170 900 300 850 360 C 930 270 975 150 1000 70 Z" fill="var(--lime)" opacity="0.9"/>
    <path class="curve-accent" d="M955 0 C 900 240 740 430 0 708 L 0 690 C 720 430 880 240 930 0 Z" fill="var(--lime)"/>
    <path class="headline-panel" d="M0 0 H930 C 880 240 720 430 0 690 Z" fill="url(#panelTone)"/>
    <rect class="base-strip" x="0" y="966" width="1000" height="12" fill="var(--green-bright)"/>
  </svg>

  <h1 class="title title-main">VEGETABLE</h1>
  <p class="title title-sub">GROWER EXPO</p>
  <div class="year-tag">2025</div>

  <div class="brand-badge">HILLCREST<br>GROWERS</div>

  <div class="photo-round photo-seedling" role="img" aria-label="Photo: a hand cupping a young green seedling in soil at sunrise"></div>
  <div class="photo-round photo-harvest" role="img" aria-label="Photo: a bowl of fresh tomatoes, cucumbers, carrots, radishes and herbs"></div>

  <div class="web-address">
    <svg viewBox="0 0 36 36" fill="none" stroke="#fff" stroke-width="2.4" aria-hidden="true">
      <circle cx="18" cy="18" r="15"/>
      <ellipse cx="18" cy="18" rx="6.5" ry="15"/>
      <line x1="3" y1="18" x2="33" y2="18"/>
      <path d="M6 10 H30 M6 26 H30"/>
    </svg>
    <span>www.website.com</span>
  </div>
</main>
</body>
</html>
```